new signage design for budget motel - Brookfern Lodge

renaming the budget motel as Brookfern Lodge, property located on side of a hill. therefore i choose to name is Brookfern Lodge, im looking for clean, modern look in signage design,this property does not have a Logo, plan to us signage design as a logo as well. current pole sign housing is rectangle shape and will be using same housing I'll be attaching picture of the signage for better idea. looking forward to awesome creative designs.

Industry/Entity Type

Motel

Font styles to use
Serif
Sans Serif

Requirements
Should not have
• mountains , mountain(s) with snow , trees, no black color, red color, blue letters, too much green.

```html
<!DOCTYPE html>
<html lang="en">
<head>
<meta charset="utf-8">
<title>Brookfern Lodge — Pole Sign</title>
<link rel="stylesheet" href="https://fonts.googleapis.com/css2?family=Montserrat:wght@400;800&display=swap">
<style>
  :root {
    --page-bg: #f2f2f2;
    --sign-blue: #2e3192;
    --sign-yellow: #ffcc00;
    --sign-white: #ffffff;
  }
  html, body {
    margin: 0;
    padding: 0;
    width: 800px;
    height: 1200px;
    overflow: hidden;
    background: var(--page-bg);
  }
  .canvas {
    position: relative;
    width: 800px;
    height: 1200px;
  }
  .sign-face {
    position: absolute;
    left: 69px;
    top: 351px;
    width: 662px;
    height: 497px;
    box-shadow: 0 2px 10px rgba(0, 0, 0, 0.18);
  }
  .sign-face svg {
    display: block;
  }
  .sign-panel { fill: var(--sign-blue); }
  .frame-solid-white { stroke: var(--sign-white); stroke-width: 4; fill: none; }
  .frame-dashed-white { stroke: var(--sign-white); stroke-width: 1; stroke-dasharray: 4 3; fill: none; }
  .frame-solid-yellow { stroke: var(--sign-yellow); stroke-width: 4; fill: none; }
  .name-primary {
    font-family: "Montserrat", sans-serif;
    font-weight: 800;
    font-size: 96px;
    fill: var(--sign-yellow);
  }
  .name-secondary {
    font-family: "Montserrat", sans-serif;
    font-weight: 400;
    font-size: 122px;
    fill: var(--sign-white);
  }
</style>
</head>
<body>
  <main class="canvas">
    <div class="sign-face">
      <svg width="662" height="497" viewBox="0 0 662 497" aria-label="Brookfern Lodge sign">
        <rect class="sign-panel" x="0" y="0" width="662" height="497"/>

        <polyline class="frame-solid-white" points="189,20 18,20 18,240"/>
        <polyline class="frame-dashed-white" points="555,17 650,17 650,119"/>
        <polyline class="frame-dashed-white" points="14,378 14,479 108,479"/>
        <polyline class="frame-solid-yellow" points="646,269 646,476 384,476"/>

        <text class="name-primary" x="331" y="240" text-anchor="middle"
              textLength="580" lengthAdjust="spacingAndGlyphs">BROOKFERN</text>
        <text class="name-secondary" x="331" y="380" text-anchor="middle">LODGE</text>
      </svg>
    </div>
  </main>
</body>
</html>
```